Design my dad a new business card because his current one sucks!

I need a business card designed for my fathers home maintenance business. His customers are individuals (single moms, old people etc.) as well as the occasional business. As such it needs to be accessible to both target audiences.

The front of the card should be dark grey on yellow with the logo and contain the following information:
- Darren Holtwick
- 0488 274 915
- info@brightoakhomecare.com.au
- 0488 274 915

- ABN: 71 284 630 912
- 'Fully Insured'

The reverse should be yellow on dark grey and will have the web address:
- brightoakhomecare.com.au

And a few key services he offers:
GENERAL REPAIRS
PAINTING/TILING/
PAVING &CONCRETING
PRESSURE WASHING
ON-SITE WELDING
DECKING ADDITIONS & REPAIRS
FENCING
FULL BOND CLEANING

This will be first time the logo has been printed so you will need to come up with the best CMYK approximation of the RGB colours to make sure it is a close as possible.

```html
<!DOCTYPE html>
<html lang="en">
<head>
<meta charset="utf-8">
<title>Bright Oak Home Care – Services Card</title>
<link rel="stylesheet" href="https://fonts.googleapis.com/css2?family=Open+Sans:wght@400;700&display=swap">
<style>
  :root {
    --bg-centre: #8f8f8f;
    --bg-mid: #7a7a7a;
    --bg-edge: #646260;
    --service-yellow: #ffff00;
    --web-white: #ffffff;
    --brand-faint: #5f5f5f;
  }
  html, body {
    margin: 0;
    padding: 0;
    width: 1200px;
    height: 686px;
    overflow: hidden;
    background: var(--bg-edge);
  }
  .card {
    position: relative;
    width: 1200px;
    height: 686px;
    overflow: hidden;
    background: radial-gradient(ellipse 70% 75% at 50% 45%, var(--bg-centre) 0%, var(--bg-mid) 45%, var(--bg-edge) 100%);
    font-family: "Open Sans", Arial, sans-serif;
  }
  .brand-mark {
    position: absolute;
    left: 0;
    right: 0;
    top: 168px;
    text-align: center;
    color: var(--brand-faint);
    font-weight: 700;
    opacity: 0.55;
    line-height: 1;
  }
  .brand-mark .brand-name {
    display: block;
    font-size: 150px;
    letter-spacing: -2px;
    text-transform: lowercase;
  }
  .brand-mark .brand-sub {
    display: block;
    margin-top: 22px;
    font-size: 40px;
    letter-spacing: 6px;
    text-transform: uppercase;
  }
  .service {
    position: absolute;
    margin: 0;
    color: var(--service-yellow);
    font-size: 36px;
    font-weight: 400;
    line-height: 1;
    white-space: nowrap;
  }
  .row-1 { top: 128px; }
  .row-2 { top: 271px; }
  .row-3 { top: 413px; }
  .row-4 { top: 553px; }
  .general-repairs { left: 57px; }
  .bond-cleaning { left: 484px; }
  .tiling { right: 63px; }
  .paving { left: 57px; }
  .pressure-washing { left: 543px; }
  .fencing { right: 64px; }
  .welding { left: 130px; }
  .decking { left: 518px; }
  .painting { left: 518px; }
  .web-address {
    position: absolute;
    left: 0;
    right: 0;
    top: 637px;
    display: flex;
    justify-content: center;
    align-items: center;
    gap: 10px;
    color: var(--web-white);
    font-size: 36px;
    line-height: 1;
    padding-left: 28px;
  }
  .pointer-icon {
    width: 24px;
    height: 32px;
    margin-top: 14px;
  }
</style>
</head>
<body>
  <main class="card">
    <div class="brand-mark" aria-label="Bright Oak Home Care">
      <span class="brand-name">bright oak</span>
      <span class="brand-sub">Home Care</span>
    </div>

    <p class="service row-1 general-repairs">GENERAL REPAIRS</p>
    <p class="service row-1 bond-cleaning">FULL BOND CLEANING</p>
    <p class="service row-1 tiling">TILING</p>

    <p class="service row-2 paving">PAVING &amp;CONCRETING</p>
    <p class="service row-2 pressure-washing">PRESSURE WASHING</p>
    <p class="service row-2 fencing">FENCING</p>

    <p class="service row-3 welding">ON-SITE WELDING</p>
    <p class="service row-3 decking">DECKING ADDITIONS &amp; REPAIRS</p>

    <p class="service row-4 painting">PAINTING</p>

    <div class="web-address">
      <span>brightoakhomecare.com.au</span>
      <svg class="pointer-icon" viewBox="0 0 24 32" aria-hidden="true">
        <path d="M2 2 L2 26 L8 20 L12 30 L16 28 L12 18 L20 18 Z" fill="#ffffff" stroke="#222222" stroke-width="1.5" stroke-linejoin="round"/>
      </svg>
    </div>
  </main>
</body>
</html>
```